Mental Health care Company in Washington DC

We are a new mental health care services provider in Washington DC. Please look at these sites.
https://brightwaterfamilysupport.com
https://www.quietharborinc.com
https://willowgate-dc.org/
https://www.tidepathdc.com
https://www.thelanternofdc.com

```html
<!DOCTYPE html>
<html lang="en">
<head>
<meta charset="utf-8">
<title>Tova Health Services</title>
<link href="https://fonts.googleapis.com/css2?family=Lato:wght@400;700;900&display=swap" rel="stylesheet">
<style>
:root{
  --navy:#0b1a3c;
  --teal:#9ed6d6;
  --teal-dark:#5fb3b3;
  --orange:#f4a35f;
  --cyan-soft:#e4fafc;
  --peach:#fee6d4;
  --page:#f7f7f7;
  --text:#3a3f4b;
  --muted:#6b7080;
  --white:#ffffff;
}
*{box-sizing:border-box;margin:0;padding:0}
html,body{width:1200px;height:3576px;overflow:hidden}
body{font-family:'Lato',sans-serif;background:var(--page);color:var(--text);position:relative}
.abs{position:absolute}

/* header */
.site-header{position:absolute;top:0;left:0;width:1200px;height:97px;background:var(--white);box-shadow:0 1px 4px rgba(0,0,0,.06);z-index:5}
.brand{position:absolute;left:111px;top:32px;font-size:28px;font-weight:700;color:var(--navy);letter-spacing:-.3px}
.main-nav{position:absolute;top:38px;left:0;width:1200px;font-size:15px;color:var(--navy)}
.main-nav a{position:absolute;color:inherit;text-decoration:none;white-space:nowrap}
.main-nav a.active{font-weight:700}

/* hero */
.hero{position:absolute;top:97px;left:0;width:1200px;height:600px;overflow:hidden}
.hero-photo{position:absolute;inset:0;background:linear-gradient(90deg,#f4f5f6 0%,#eef1f4 30%,#cfdbe6 55%,#aebfd0 75%,#c9a58a 90%,#b98d6e 100%)}
.hero-curve{position:absolute;left:0;top:0}
.hero-copy{position:absolute;left:111px;top:115px;width:460px}
.hero-copy h1{font-size:50px;line-height:59px;font-weight:900;color:var(--navy)}
.hero-copy p{margin-top:38px;font-size:17px;line-height:26px;color:var(--text)}
.btn-soft{display:inline-block;background:var(--teal);color:var(--navy);font-size:15px;padding:10px 24px;border:1px solid var(--teal-dark);text-decoration:none}
.hero-copy .btn-soft{margin-top:26px}

/* section headings */
.eyebrow{font-size:23px;color:var(--navy)}
.section-title{font-size:38px;line-height:45px;font-weight:700;color:var(--navy)}
.section-intro{font-size:15px;line-height:26px;color:var(--text)}

/* services */
.service-card{position:absolute;top:918px;width:222px;height:295px;background:var(--navy);border-radius:6px;text-align:center;color:var(--white)}
.service-card svg{margin-top:28px}
.service-card h3{margin-top:14px;font-size:19px;font-weight:400;color:var(--teal)}
.service-card p{margin:20px 16px 0;font-size:12.5px;line-height:20px}
.service-card .btn-outline{display:inline-block;margin-top:30px;width:144px;padding:5px 0;border:1px solid var(--white);color:var(--white);font-size:15px;text-decoration:none}
.service-card::after{content:"";position:absolute;left:55px;bottom:-4px;width:112px;height:6px;border-radius:3px;background:var(--orange)}

/* about */
.peach-band{position:absolute;top:1643px;left:0;width:1200px;height:996px;background:var(--peach)}
.about-box{position:absolute;top:1302px;left:111px;width:979px;height:552px;border:2px solid var(--orange);border-radius:22px;overflow:hidden;background:var(--cyan-soft)}
.about-photo{position:absolute;left:0;top:0;width:503px;height:100%;background:linear-gradient(135deg,#d9dcd8 0%,#a9b3ad 40%,#8fa7bd 70%,#5c6f8c 100%)}
.about-copy{position:absolute;left:546px;top:118px;width:404px}
.about-copy p{margin-top:28px;font-size:15px;line-height:26px}
.about-copy .btn-soft{margin-top:24px}

/* treatment */
.treat-card{position:absolute;top:2129px;width:294px;height:424px;background:var(--white);border-radius:6px;box-shadow:0 2px 8px rgba(0,0,0,.1);overflow:hidden}
.treat-photo{height:208px}
.treat-card h3{margin:26px 16px 0;font-size:19px;font-weight:400;color:var(--navy)}
.treat-card p{margin:18px 18px 0;font-size:13px;line-height:19px;color:var(--muted)}
.treat-foot{position:absolute;left:0;bottom:0;width:100%;height:44px;border-top:1px solid #e3e3e3}
.treat-foot a{position:absolute;left:18px;top:13px;font-size:14px;color:var(--navy)}
.treat-foot svg{position:absolute;right:16px;top:12px}

/* testimonials */
.quote-card{position:absolute;top:2885px;width:296px;height:290px;border:1px solid #8a8f99;border-radius:8px;background:var(--white)}
.quote-card .stars{position:absolute;right:24px;top:34px}
.quote-card .mark{position:absolute;left:20px;top:22px;font-size:42px;font-weight:900;color:var(--navy);font-family:Georgia,serif;line-height:1}
.quote-card p{position:absolute;left:20px;top:80px;width:258px;font-size:13px;line-height:21px;color:var(--muted)}
.avatar{position:absolute;left:20px;top:212px;width:45px;height:45px;border-radius:50%;background:var(--orange);color:var(--white);font-size:21px;line-height:45px;text-align:center}
.person{position:absolute;left:82px;top:212px}
.person strong{display:block;font-size:19px;font-weight:700;color:var(--navy)}
.person span{font-size:12.5px;color:var(--muted)}
.dots{position:absolute;top:3217px;left:564px;display:flex;gap:10px;align-items:center}
.dots i{display:block;width:10px;height:10px;border-radius:50%;background:#8a8f99}
.dots i.on{width:14px;height:14px;background:var(--teal-dark)}

/* footer */
.site-footer{position:absolute;top:3317px;left:0;width:1200px;height:259px;background:var(--navy);color:var(--white)}
.footer-brand{position:absolute;top:56px;width:100%;text-align:center;font-size:38px;font-weight:700}
.footer-rule{position:absolute;left:111px;width:979px;height:1px;background:rgba(255,255,255,.6)}
.footer-nav{position:absolute;top:170px;width:100%;text-align:center;font-size:15px}
.footer-nav a{color:var(--white);text-decoration:none;margin:0 16px}
.copyright{position:absolute;left:111px;top:221px;font-size:12.5px;color:#c9cfdc}
.legal{position:absolute;right:110px;top:221px;font-size:12.5px;color:#c9cfdc}
.legal span{margin:0 8px}
</style>
</head>
<body>

<header class="site-header">
  <div class="brand">Tova Health Services</div>
  <nav class="main-nav">
    <a class="active" style="left:492px">Home</a>
    <a style="left:570px">About Us</a>
    <a style="left:669px">Services</a>
    <a style="left:761px">Therapies &amp; Treatment</a>
    <a style="left:951px">Gallery</a>
    <a style="left:1036px">Contact</a>
  </nav>
</header>

<section class="hero">
  <div class="hero-photo" role="img" aria-label="Hands from many people joined into a heart shape against a bright cloudy sky"></div>
  <svg class="hero-curve" width="1200" height="600" viewBox="0 0 1200 600" aria-hidden="true">
    <path d="M0 459 Q600 640 1200 459 L1200 600 L0 600 Z" fill="#f7f7f7"/>
    <path d="M132 507 Q600 660 1056 507 Q600 620 132 507 Z" fill="#f4a35f"/>
  </svg>
  <div class="hero-copy">
    <h1>Your Wellness Starts With Us</h1>
    <p>Lorem ipsum dolor sit amet, consectetur adipiscing elit, sed do eiusmod tempor incididunt ut labore et dolore magna aliqua. Quis ipsum suspendisse ultrices gravida.</p>
    <a class="btn-soft">Make An Appointment</a>
  </div>
</section>

<section class="services">
  <div class="abs eyebrow" style="left:111px;top:795px">How We Help You</div>
  <h2 class="abs section-title" style="left:111px;top:829px">Our Services</h2>
  <p class="abs section-intro" style="left:539px;top:833px;width:555px">Lorem ipsum dolor sit amet, consectetur adipiscing elit, sed do eiusmod tempor inc dunt ut labore et dolore magna aliqua.</p>

  <article class="service-card" style="left:111px">
    <svg width="54" height="54" viewBox="0 0 54 54" fill="none" stroke="#f4a35f" stroke-width="2"><circle cx="27" cy="20" r="12"/><path d="M27 14v12M21 20h12M6 30c4 6 10 16 21 16s17-10 21-16"/></svg>
    <h3>Medical Services</h3>
    <p>Lorem ipsum dolor sit amet, consectetur adipiscing elit, sed do eiusmod tempor incididunt ut</p>
    <a class="btn-outline">Learn More</a>
  </article>
  <article class="service-card" style="left:364px">
    <svg width="54" height="54" viewBox="0 0 54 54" fill="none" stroke="#f4a35f" stroke-width="2"><circle cx="27" cy="27" r="22"/><circle cx="28" cy="24" r="9"/><path d="M12 38h8M16 34v8"/></svg>
    <h3>Behavioral Health</h3>
    <p>Lorem ipsum dolor sit amet, consectetur adipiscing elit, sed do eiusmod tempor incididunt ut</p>
    <a class="btn-outline">Learn More</a>
  </article>
  <article class="service-card" style="left:615px">
    <svg width="54" height="54" viewBox="0 0 54 54" fill="none" stroke="#f4a35f" stroke-width="2"><circle cx="27" cy="15" r="5"/><path d="M19 28c0-5 16-5 16 0M6 38c6-4 12-4 18 0h10l12-8M6 46h30"/></svg>
    <h3>Human Services</h3>
    <p>Lorem ipsum dolor sit amet, consectetur adipiscing elit, sed do eiusmod tempor incididunt ut</p>
    <a class="btn-outline">Learn More</a>
  </article>
  <article class="service-card" style="left:867px">
    <svg width="54" height="54" viewBox="0 0 54 54" fill="none" stroke="#f4a35f" stroke-width="2"><path d="M27 8c7 8 7 22 0 32c-7-10-7-24 0-32zM27 40c-8-2-16-8-18-20c8 0 14 6 18 20zM27 40c8-2 16-8 18-20c-8 0-14 6-18 20zM10 44h34"/></svg>
    <h3>Spiritual Needs</h3>
    <p>Lorem ipsum dolor sit amet, consectetur adipiscing elit, sed do eiusmod tempor incididunt ut</p>
    <a class="btn-outline">Learn More</a>
  </article>
</section>

<div class="peach-band"></div>

<section class="about-box">
  <div class="about-photo" role="img" aria-label="A smiling nurse in blue scrubs supporting an older woman by the arm"></div>
  <div class="about-copy">
    <div class="eyebrow">About Us</div>
    <h2 class="section-title" style="margin-top:6px">Caring for Our Community</h2>
    <p>Lorem ipsum dolor sit amet, consectetur adipiscing elit, sed do eiusmod tempor inc dunt ut labore et dolore magna aliqua.&nbsp; Ut enim ad minim veniam, quis nostrud exercitation ullamco laboris nisi ut aliquip ex ea commodo consequat. Duis aute irure dolor in reprehenderit in voluptate velit esse cillum dolore eu fugiat nulla pariatur.</p>
    <a class="btn-soft">Read More</a>
  </div>
</section>

<section class="treatment">
  <div class="abs eyebrow" style="left:111px;top:1964px">Our Commitment to You</div>
  <h2 class="abs section-title" style="left:111px;top:1999px;width:320px">Our Treatment Approach</h2>
  <p class="abs section-intro" style="left:539px;top:2020px;width:555px">Lorem ipsum dolor sit amet, consectetur adipiscing elit, sed do eiusmod tempor inc dunt ut labore et dolore magna aliqua.</p>

  <article class="treat-card" style="left:111px">
    <div class="treat-photo" role="img" aria-label="A distressed man on a sofa talking with a counselor" style="background:linear-gradient(135deg,#c9c6c0,#8a8580 60%,#5b5a5c)"></div>
    <h3>Depression &amp; Anxiety</h3>
    <p>Sed ut perspiciatis unde omnis iste natus error sit voluptatem accusantium doloremque laudantium, totam rem aperiam, eaque ipsa quae ab illo</p>
    <div class="treat-foot"><a>Click Here</a><svg width="20" height="20" viewBox="0 0 20 20"><circle cx="10" cy="10" r="10" fill="#1b1f2a"/><path d="M6 10h7M10 6.5l3.5 3.5L10 13.5" stroke="#fff" stroke-width="2" fill="none"/></svg></div>
  </article>
  <article class="treat-card" style="left:454px">
    <div class="treat-photo" role="img" aria-label="A woman in a therapy session speaking with a therapist in a bright room" style="background:linear-gradient(135deg,#e6e8e2,#bfc7b8 55%,#6f6a66)"></div>
    <h3>Trauma &amp; PTSD</h3>
    <p>Sed ut perspiciatis unde omnis iste natus error sit voluptatem accusantium doloremque laudantium, totam rem aperiam, eaque ipsa quae ab illo</p>
    <div class="treat-foot"><a>Click Here</a><svg width="20" height="20" viewBox="0 0 20 20"><circle cx="10" cy="10" r="10" fill="#1b1f2a"/><path d="M6 10h7M10 6.5l3.5 3.5L10 13.5" stroke="#fff" stroke-width="2" fill="none"/></svg></div>
  </article>
  <article class="treat-card" style="left:796px">
    <div class="treat-photo" role="img" aria-label="A young couple sitting together on a couch during counseling" style="background:linear-gradient(135deg,#dfe3e6,#b7bcbf 55%,#7d7570)"></div>
    <h3>Relationship</h3>
    <p>Sed ut perspiciatis unde omnis iste natus error sit voluptatem accusantium doloremque laudantium, totam rem aperiam, eaque ipsa quae ab illo</p>
    <div class="treat-foot"><a>Click Here</a><svg width="20" height="20" viewBox="0 0 20 20"><circle cx="10" cy="10" r="10" fill="#1b1f2a"/><path d="M6 10h7M10 6.5l3.5 3.5L10 13.5" stroke="#fff" stroke-width="2" fill="none"/></svg></div>
  </article>
</section>

<section class="testimonials">
  <div class="abs eyebrow" style="left:111px;top:2746px">Testimonials</div>
  <h2 class="abs section-title" style="left:111px;top:2781px">Trusted by Those We Serve</h2>
  <p class="abs section-intro" style="left:632px;top:2778px;width:460px">Lorem ipsum dolor sit amet, consectetur adipiscing elit, sed do eiusmod tempor inc dunt ut labore et dolore magna aliqua.</p>

  <article class="quote-card" style="left:112px">
    <span class="mark">&ldquo;</span>
    <svg class="stars" width="64" height="12" viewBox="0 0 64 12" fill="#f4a35f"><g id="star"><path d="M6 0l1.8 4H12L8.6 6.6 9.8 11 6 8.4 2.2 11 3.4 6.6 0 4h4.2z"/></g><use href="#star" x="13"/><use href="#star" x="26"/><use href="#star" x="39"/><use href="#star" x="52"/></svg>
    <p>Lorem ipsum dolor sit amet, consectetur adipiscing elit, sed do eiusmod tempor incididunt ut labore et dolore magna aliqua. Quis ipsum suspendisse ultrices gravida. Risus commodo viverra maecenas accumsan</p>
    <div class="avatar">MC</div>
    <div class="person"><strong>Maya Collins</strong><span>MD at Northfield Groups</span></div>
  </article>
  <article class="quote-card" style="left:453px">
    <span class="mark">&ldquo;</span>
    <svg class="stars" width="64" height="12" viewBox="0 0 64 12" fill="#f4a35f"><use href="#star"/><use href="#star" x="13"/><use href="#star" x="26"/><use href="#star" x="39"/><use href="#star" x="52"/></svg>
    <p>Lorem ipsum dolor sit amet, consectetur adipiscing elit, sed do eiusmod tempor incididunt ut labore et dolore magna aliqua. Quis ipsum suspendisse ultrices gravida. Risus commodo viverra maecenas accumsan</p>
    <div class="avatar">MC</div>
    <div class="person"><strong>Maya Collins</strong><span>MD at Northfield Groups</span></div>
  </article>
  <article class="quote-card" style="left:793px">
    <span class="mark">&ldquo;</span>
    <svg class="stars" width="64" height="12" viewBox="0 0 64 12" fill="#f4a35f"><use href="#star"/><use href="#star" x="13"/><use href="#star" x="26"/><use href="#star" x="39"/><use href="#star" x="52"/></svg>
    <p>Lorem ipsum dolor sit amet, consectetur adipiscing elit, sed do eiusmod tempor incididunt ut labore et dolore magna aliqua. Quis ipsum suspendisse ultrices gravida. Risus commodo viverra maecenas accumsan</p>
    <div class="avatar">MC</div>
    <div class="person"><strong>Maya Collins</strong><span>MD at Northfield Groups</span></div>
  </article>

  <div class="dots"><i class="on"></i><i></i><i></i><i></i></div>
</section>

<footer class="site-footer">
  <div class="footer-brand">Tova Health Services</div>
  <div class="footer-rule" style="top:155px"></div>
  <nav class="footer-nav">
    <a>Home</a><a>About Us</a><a>Services</a><a>Therapies &amp; Treatment</a><a>Gallery</a><a>Contact</a>
  </nav>
  <div class="footer-rule" style="top:204px"></div>
  <div class="copyright">Copyright &copy; 2025 Tova Health Services. All rights reserved.</div>
  <div class="legal">Privacy Policy<span>|</span>Terms &amp; Conditions<span>|</span>Cookie Policy</div>
</footer>

</body>
</html>
```